QuillVane needs a dashboard page designed

Redesign the dashboard shown in the provided images.

There are two images:
- dashboard.png
- dashboard-expanded.png

NOTE: The vocabulary navigation on the left will be a very long list of words 100s, so keep that in mind when you're designing both the vocab navigation and the expanded vocab popup.

In the dashboard.png picture, there needs to be a progress chart showing the word progress like the following: review 1(show it as completed) -> review 2(show the user they are here) -> review 3(unvisited) -> review 4(unvisited)

The do-not-design-this-page.png image is for your reference only. It is not to be designed. Use it to understand the overall look and feel of the website to help you create the best dashboard page possible.
Updates

Need extra days to review

Industry/Entity Type

Education English learning

Number of Pages Required

1 page

Requirements
Must have
• The main navigation and main header cannot change between pages. See the do-not-design page for the main navigateion and header.
Should not have
• Do not add a person profile. We will not have images of our users. Keep the icons in the main navigation as they are.

```html
<!DOCTYPE html>
<html lang="en">
<head>
<meta charset="utf-8">
<title>QuillVane – LexiPath Tutor Dashboard</title>
<link href="https://fonts.googleapis.com/css2?family=Nunito+Sans:wght@400;600;700;800&display=swap" rel="stylesheet">
<style>
:root{
  --page:#010f20;
  --navy:#1d2380;
  --blue:#2e67b8;
  --pale:#eceef8;
  --step-idle:#eef0f8;
  --orange:#f7a21b;
  --teal:#33c1bd;
  --ink:#222;
  --body:#3a3a3a;
  --chip:#4a4a4a;
  --rule:#dcdcdc;
  --white:#fff;
}
*{box-sizing:border-box;margin:0;padding:0}
html,body{width:744px;height:1200px;overflow:hidden;background:var(--page)}
body{font-family:"Nunito Sans",sans-serif;color:var(--ink)}
.stage{position:absolute;left:0;top:0;width:1512px;height:2438px;transform:scale(0.49206);transform-origin:0 0}
.screen{position:absolute;left:119px;width:1228px;height:1051px;background:var(--white);overflow:hidden}
.screen--main{top:127px}
.screen--popup{top:1260px}
.abs{position:absolute}
.topbar{left:0;top:0;width:1228px;height:63px;background:var(--navy);color:var(--white)}
.brand{left:25px;top:13px;font-size:26px;font-weight:600;letter-spacing:.2px;white-space:nowrap}
.topbar-divider{left:207px;top:14px;width:3px;height:34px;background:var(--white)}
.product{left:249px;top:20px;font-size:16px;font-weight:600;display:flex;align-items:center;gap:12px;white-space:nowrap}
.top-icons{left:1115px;top:17px;display:flex;gap:14px;align-items:center}
.rail{left:0;top:63px;width:121px;height:935px;background:var(--pale)}
.rail-item{position:absolute;left:0;width:121px;display:flex;flex-direction:column;align-items:center;gap:6px;font-size:12.5px;font-weight:600;color:var(--navy);white-space:nowrap}
.rail-item.is-active{background:var(--navy);color:var(--white);top:17px;height:75px;justify-content:center}
.rail-sep{position:absolute;left:0;width:121px;height:2px;background:var(--white)}
.vocab{left:121px;top:63px;width:263px;height:935px;background:var(--white);box-shadow:3px 0 6px rgba(0,0,0,.06)}
.select{position:absolute;width:180px;height:33px;border:1px solid var(--navy);font-size:11px;padding:8px 12px;display:flex;justify-content:space-between;align-items:center;background:var(--white)}
.group-title{position:absolute;font-size:13.5px;font-weight:700;color:var(--ink);white-space:nowrap}
.current-word{position:absolute;font-size:13.5px;font-weight:800;color:var(--navy)}
.word-list{position:absolute;list-style:none;font-size:13.5px;color:#444;line-height:24.5px;white-space:nowrap}
.rule{position:absolute;height:1px;background:var(--rule)}
.steps{left:427px;top:98px}
.word-title{left:426px;top:184px;font-size:26px;font-weight:800;color:var(--navy)}
.cta{left:913px;top:181px;width:292px;height:43px;background:var(--orange);color:var(--white);font-weight:800;font-size:15px;display:flex;align-items:center;justify-content:center;white-space:nowrap}
.definition{left:426px;top:252px;width:780px;font-size:14.5px;line-height:21.3px;color:var(--body);text-align:justify}
.chart-card{left:428px;top:363px;width:773px;height:417px;background:var(--white);box-shadow:0 0 8px rgba(0,0,0,.08)}
.chart-title{left:0;top:36px;width:753px;text-align:center;font-size:17px;font-weight:800;color:var(--navy)}
.analysis-title{left:427px;top:830px;font-size:20px;font-weight:800;color:var(--navy);white-space:nowrap}
.analysis{left:427px;top:875px;width:779px;font-size:14.5px;line-height:19.6px;color:var(--body);text-align:justify}
.footer{left:0;top:998px;width:1228px;height:53px;background:var(--blue);color:var(--white);font-size:14px;display:flex;align-items:center;justify-content:center}
.dim{left:0;top:0;width:1228px;height:1051px;background:rgba(0,0,0,.78)}
.modal{left:185px;top:343px;width:858px;height:365px;background:var(--white)}
.chips{position:absolute;display:flex;gap:7px;flex-wrap:nowrap}
.chip{flex:0 0 auto;white-space:nowrap;background:var(--chip);color:var(--white);font-size:13px;line-height:1;height:28px;padding:0 9px;display:flex;align-items:center;border:1px solid #333}
</style>
</head>
<body>
<div class="stage">

  <!-- Dashboard -->
  <section class="screen screen--main">
    <header class="abs topbar">
      <div class="abs brand">QuillVane</div>
      <div class="abs topbar-divider"></div>
      <div class="abs product">LexiPath Tutor
        <svg width="14" height="9" viewBox="0 0 14 9"><path d="M1 1l6 6 6-6" fill="none" stroke="#fff" stroke-width="2"/></svg></div>
      <div class="abs top-icons">
        <svg width="26" height="26" viewBox="0 0 24 24"><path fill="#fff" d="M19.4 13a7.5 7.5 0 0 0 0-2l2.1-1.6-2-3.4-2.5 1a7 7 0 0 0-1.7-1L15 3.3h-4l-.3 2.7a7 7 0 0 0-1.7 1l-2.5-1-2 3.4L6.6 11a7.5 7.5 0 0 0 0 2l-2.1 1.6 2 3.4 2.5-1a7 7 0 0 0 1.7 1l.3 2.7h4l.3-2.7a7 7 0 0 0 1.7-1l2.5 1 2-3.4zM13 15.5a3.5 3.5 0 1 1 0-7 3.5 3.5 0 0 1 0 7z"/></svg>
        <svg width="44" height="28" viewBox="0 0 44 28"><circle cx="12" cy="7" r="6.5" fill="#fff"/><path d="M0 28c0-8 5-12 12-12s12 4 12 12z" fill="#fff"/><path d="M32 12l5 5 5-5" fill="none" stroke="#fff" stroke-width="2"/></svg>
      </div>
    </header>

    <nav class="abs rail">
      <div class="rail-item is-active">
        <svg width="26" height="26" viewBox="0 0 26 26"><path d="M3 12L13 3l10 9M6 10v13h5v-7h4v7h5V10" fill="none" stroke="#fff" stroke-width="1.6"/></svg>
        LexiPath Tutor</div>
      <div class="rail-item" style="top:120px">
        <svg width="28" height="28" viewBox="0 0 28 28"><path d="M3 9l6-2 7 3 6-2v16l-6 2-7-3-6 2zM9 7v16M16 10v16" fill="none" stroke="#1d2380" stroke-width="1.6"/><circle cx="21" cy="6" r="3" fill="none" stroke="#1d2380" stroke-width="1.6"/></svg>
        Daily English</div>
      <div class="rail-sep" style="top:198px"></div>
      <div class="rail-item" style="top:228px">
        <svg width="28" height="26" viewBox="0 0 28 26"><rect x="3" y="7" width="22" height="16" rx="2" fill="none" stroke="#1d2380" stroke-width="1.6"/><path d="M10 7V3h8v4M3 14h22M12 14v3h4v-3" fill="none" stroke="#1d2380" stroke-width="1.6"/></svg>
        Business</div>
    </nav>

    <aside class="abs vocab">
      <div class="select" style="left:21px;top:19px">All
        <svg width="14" height="9" viewBox="0 0 14 9"><path d="M1 1l6 6 6-6" fill="none" stroke="#1d2380" stroke-width="1.8"/></svg></div>
      <svg class="abs" style="left:221px;top:26px" width="20" height="20" viewBox="0 0 20 20"><path d="M13 2h5v5M2 13v5h5" fill="none" stroke="#1d2380" stroke-width="2"/></svg>
      <div class="group-title" style="left:22px;top:81px">Short-Term Memory</div>
      <div class="current-word" style="left:22px;top:104px">Grap</div>
      <div class="rule" style="left:17px;top:143px;width:233px"></div>
      <div class="group-title" style="left:22px;top:162px">Working Memory</div>
      <ul class="word-list" style="left:22px;top:188px">
        <li>Cool Down</li><li>Crave</li><li>Go For</li><li>Go-To</li><li>In The Mood For</li><li>Sip</li><li>Soothing</li><li>Stick With</li><li>Throw In/Throw On</li>
      </ul>
      <div class="rule" style="left:17px;top:437px;width:233px"></div>
      <div class="group-title" style="left:22px;top:468px">Long-Term Memory</div>
      <ul class="word-list" style="left:22px;top:494px"><li>Give It A Try</li></ul>
    </aside>

    <svg class="abs steps" width="540" height="44" viewBox="0 0 540 44" role="img" aria-label="Review progress: review 1 complete, review 2 current">
      <polygon points="0,0 105,0 120,21 105,42 0,42" fill="#2e67b8"/>
      <polygon points="127,0 232,0 247,21 232,42 127,42 142,21" fill="#1d2380"/>
      <polygon points="265,0 370,0 385,21 370,42 265,42 280,21" fill="#eef0f8"/>
      <polygon points="402,0 507,0 522,21 507,42 402,42 417,21" fill="#eef0f8"/>
      <g font-family="Nunito Sans, sans-serif" font-size="15.5" text-anchor="middle">
        <text x="55" y="26" fill="#fff">Review 1</text>
        <text x="193" y="26" fill="#fff">Review 2</text>
        <text x="332" y="26" fill="#1d2380">Review 3</text>
        <text x="469" y="26" fill="#1d2380">Review 4</text>
      </g>
    </svg>

    <h1 class="abs word-title">GRAP</h1>
    <div class="abs cta">Start Vocabulary Review Exercise 3</div>
    <p class="abs definition">The word "grab" is most commonly used as a verb, meaning to take something quickly or suddenly. Imagine you're running late for school. You don't have time for breakfast, so you quickly grab an apple from the kitchen and rush out the door. As you reach the bus stop, your friend waves and says, Hey! Let's grab a coffee after class. Later, when you sit down, your phone starts ringing. You grab it from your bag and answer.</p>

    <div class="abs chart-card">
      <div class="abs chart-title">Learning Curve Graph</div>
      <svg class="abs" style="left:0;top:0" width="773" height="417" viewBox="428 363 773 417" role="img" aria-label="Learning curve area chart from 18 to 26 May">
        <polygon fill="#33c1bd" points="496,713 541,658 593,521 643,581 693,549 743,559 793,501 843,625 894,551 944,583 994,480 1043,513 1044,563 1074,583 1124,480 1174,513 1174,715 491,715"/>
        <line x1="491" y1="415" x2="491" y2="716" stroke="#3a3f4a" stroke-width="3"/>
        <line x1="490" y1="715" x2="1176" y2="715" stroke="#3a3f4a" stroke-width="3"/>
        <g font-family="Nunito Sans, sans-serif" font-size="14" fill="#555" text-anchor="end">
          <text x="472" y="472">100</text><text x="472" y="522">80</text><text x="472" y="572">60</text>
          <text x="472" y="622">40</text><text x="472" y="673">20</text><text x="472" y="715">0</text>
        </g>
        <g font-family="Nunito Sans, sans-serif" font-size="11.5" fill="#555" text-anchor="middle">
          <text x="511" y="744">18</text><text x="591" y="744">19</text><text x="671" y="744">20</text><text x="747" y="744">21</text><text x="822" y="744">22</text><text x="891" y="744">23</text><text x="961" y="744">24</text><text x="1041" y="744">25</text><text x="1122" y="744">26</text>
          <text x="548" y="744">12:00</text><text x="628" y="744">12:00</text><text x="706" y="744">12:00</text><text x="780" y="744">12:00</text><text x="853" y="744">12:00</text><text x="926" y="744">12:00</text><text x="996" y="744">12:00</text><text x="1075" y="744">12:00</text><text x="1158" y="744">12:00</text>
        </g>
        <g font-family="Nunito Sans, sans-serif" font-size="9" fill="#777" text-anchor="middle">
          <text x="511" y="757">May</text><text x="591" y="757">May</text><text x="671" y="757">May</text><text x="747" y="757">May</text><text x="822" y="757">May</text><text x="891" y="757">May</text><text x="961" y="757">May</text><text x="1041" y="757">May</text><text x="1122" y="757">May</text>
        </g>
      </svg>
    </div>

    <h2 class="abs analysis-title">LexiPath Tutor Learning Analysis</h2>
    <p class="abs analysis">Lorem ipsum dolor sit amet, consectetur adipiscing elit, sed do eiusmod tempor incididunt ut labore et dolore magna aliqua. Ut enim ad minim veniam, quis nostrud exercitation ullamco laboris nisi ut aliquip ex ea commodo consequat. Duis aute irure dolor in reprehenderit in voluptate velit esse cillum dolore eu fugiat nulla pariatur. Excepteur sint occaecat cupidatat non proident, sunt in culpa qui officia deserunt mollit anim id est laborum.</p>

    <footer class="abs footer">Copyright © 2025 All Rights Reserved</footer>
  </section>

  <!-- Dashboard with expanded vocabulary -->
  <section class="screen screen--popup">
    <header class="abs topbar">
      <div class="abs brand">QuillVane</div>
      <div class="abs topbar-divider"></div>
      <div class="abs product">LexiPath Tutor
        <svg width="14" height="9" viewBox="0 0 14 9"><path d="M1 1l6 6 6-6" fill="none" stroke="#fff" stroke-width="2"/></svg></div>
      <div class="abs top-icons">
        <svg width="26" height="26" viewBox="0 0 24 24"><path fill="#fff" d="M19.4 13a7.5 7.5 0 0 0 0-2l2.1-1.6-2-3.4-2.5 1a7 7 0 0 0-1.7-1L15 3.3h-4l-.3 2.7a7 7 0 0 0-1.7 1l-2.5-1-2 3.4L6.6 11a7.5 7.5 0 0 0 0 2l-2.1 1.6 2 3.4 2.5-1a7 7 0 0 0 1.7 1l.3 2.7h4l.3-2.7a7 7 0 0 0 1.7-1l2.5 1 2-3.4zM13 15.5a3.5 3.5 0 1 1 0-7 3.5 3.5 0 0 1 0 7z"/></svg>
        <svg width="44" height="28" viewBox="0 0 44 28"><circle cx="12" cy="7" r="6.5" fill="#fff"/><path d="M0 28c0-8 5-12 12-12s12 4 12 12z" fill="#fff"/><path d="M32 12l5 5 5-5" fill="none" stroke="#fff" stroke-width="2"/></svg>
      </div>
    </header>

    <nav class="abs rail">
      <div class="rail-item is-active">
        <svg width="26" height="26" viewBox="0 0 26 26"><path d="M3 12L13 3l10 9M6 10v13h5v-7h4v7h5V10" fill="none" stroke="#fff" stroke-width="1.6"/></svg>
        LexiPath Tutor</div>
      <div class="rail-item" style="top:120px">
        <svg width="28" height="28" viewBox="0 0 28 28"><path d="M3 9l6-2 7 3 6-2v16l-6 2-7-3-6 2zM9 7v16M16 10v16" fill="none" stroke="#1d2380" stroke-width="1.6"/><circle cx="21" cy="6" r="3" fill="none" stroke="#1d2380" stroke-width="1.6"/></svg>
        Daily English</div>
      <div class="rail-sep" style="top:198px"></div>
      <div class="rail-item" style="top:228px">
        <svg width="28" height="26" viewBox="0 0 28 26"><rect x="3" y="7" width="22" height="16" rx="2" fill="none" stroke="#1d2380" stroke-width="1.6"/><path d="M10 7V3h8v4M3 14h22M12 14v3h4v-3" fill="none" stroke="#1d2380" stroke-width="1.6"/></svg>
        Business</div>
    </nav>

    <aside class="abs vocab">
      <div class="select" style="left:21px;top:19px">All
        <svg width="14" height="9" viewBox="0 0 14 9"><path d="M1 1l6 6 6-6" fill="none" stroke="#1d2380" stroke-width="1.8"/></svg></div>
      <svg class="abs" style="left:221px;top:26px" width="20" height="20" viewBox="0 0 20 20"><path d="M13 2h5v5M2 13v5h5" fill="none" stroke="#1d2380" stroke-width="2"/></svg>
      <div class="group-title" style="left:22px;top:81px">Short-Term Memory</div>
      <div class="current-word" style="left:22px;top:104px">Grap</div>
      <div class="rule" style="left:17px;top:143px;width:233px"></div>
      <div class="group-title" style="left:22px;top:162px">Working Memory</div>
      <ul class="word-list" style="left:22px;top:188px">
        <li>Cool Down</li><li>Crave</li><li>Go For</li><li>Go-To</li><li>In The Mood For</li><li>Sip</li><li>Soothing</li><li>Stick With</li><li>Throw In/Throw On</li>
      </ul>
      <div class="rule" style="left:17px;top:437px;width:233px"></div>
      <div class="group-title" style="left:22px;top:468px">Long-Term Memory</div>
      <ul class="word-list" style="left:22px;top:494px"><li>Give It A Try</li></ul>
    </aside>

    <svg class="abs steps" width="540" height="44" viewBox="0 0 540 44" role="img" aria-label="Review progress">
      <polygon points="0,0 105,0 120,21 105,42 0,42" fill="#2e67b8"/>
      <polygon points="127,0 232,0 247,21 232,42 127,42 142,21" fill="#1d2380"/>
      <polygon points="265,0 370,0 385,21 370,42 265,42 280,21" fill="#eef0f8"/>
      <polygon points="402,0 507,0 522,21 507,42 402,42 417,21" fill="#eef0f8"/>
      <g font-family="Nunito Sans, sans-serif" font-size="15.5" text-anchor="middle">
        <text x="55" y="26" fill="#fff">Review 1</text><text x="193" y="26" fill="#fff">Review 2</text>
        <text x="332" y="26" fill="#1d2380">Review 3</text><text x="469" y="26" fill="#1d2380">Review 4</text>
      </g>
    </svg>

    <h1 class="abs word-title">GRAP</h1>
    <div class="abs cta">Start Vocabulary Review Exercise 3</div>
    <p class="abs definition">The word "grab" is most commonly used as a verb, meaning to take something quickly or suddenly. Imagine you're running late for school. You don't have time for breakfast, so you quickly grab an apple from the kitchen and rush out the door. As you reach the bus stop, your friend waves and says, Hey! Let's grab a coffee after class. Later, when you sit down, your phone starts ringing. You grab it from your bag and answer.</p>

    <h2 class="abs analysis-title">LexiPath Tutor Learning Analysis</h2>
    <p class="abs analysis">Lorem ipsum dolor sit amet, consectetur adipiscing elit, sed do eiusmod tempor incididunt ut labore et dolore magna aliqua. Ut enim ad minim veniam, quis nostrud exercitation ullamco laboris nisi ut aliquip ex ea commodo consequat. Duis aute irure dolor in reprehenderit in voluptate velit esse cillum dolore eu fugiat nulla pariatur. Excepteur sint occaecat cupidatat non proident, sunt in culpa qui officia deserunt mollit anim id est laborum.</p>

    <footer class="abs footer">Copyright © 2025 All Rights Reserved</footer>

    <div class="abs dim"></div>

    <div class="abs modal" role="dialog" aria-label="All vocabulary">
      <svg class="abs" style="left:813px;top:15px" width="30" height="30" viewBox="0 0 30 30"><path d="M2 2l26 26M28 2L2 28" stroke="#111" stroke-width="2.2"/></svg>
      <div class="select" style="left:39px;top:41px">All
        <svg width="14" height="9" viewBox="0 0 14 9"><path d="M1 1l6 6 6-6" fill="none" stroke="#1d2380" stroke-width="1.8"/></svg></div>
      <div class="group-title" style="left:36px;top:102px">Short-Term Memory</div>
      <div class="current-word" style="left:36px;top:125px">Grap</div>
      <div class="group-title" style="left:36px;top:170px">Working Memory</div>
      <div class="chips" style="left:37px;top:199px">
        <span class="chip">Cool Down</span><span class="chip" style="padding:0 14px">Crave</span><span class="chip">Go For</span><span class="chip">Go-To</span><span class="chip">In The Mood For</span><span class="chip">Sip</span><span class="chip">Soothing</span><span class="chip">Stick With</span><span class="chip">Throw In/Throw On</span>
      </div>
      <div class="group-title" style="left:36px;top:256px">Long-Term Memory</div>
      <div class="chips" style="left:37px;top:287px"><span class="chip">Give It A Try</span></div>
    </div>
  </section>

</div>
</body>
</html>
```